VKT Consulting

Government/Entitlement Consulting Services- I assist developers obtain entitlements from local, state and federal government agencies so that they can build their projects. Often these projects are very complicated and political and may face community opposition.

Target Market(s)

Real Estate Developers

Industry/Entity Type

Business Consultant

Contact Information for Business Card

Dana Melbrook
Principal

Font styles to use
Serif
Sans Serif

Requirements
Must have
• Classy and professional appeal.
Nice to have
• I like a combination of a mat and glossy finish. I've seen that done with black and then a bold color for a pop, but am not 100% committed to that.

```html
<!DOCTYPE html>
<html lang="en">
<head>
<meta charset="utf-8">
<title>VKT Consulting – Business Card</title>
<link rel="stylesheet" href="https://fonts.googleapis.com/css2?family=Arimo:wght@400;700&display=swap">
<style>
  :root {
    --stage: #e9e7e3;
    --blue: #19a3dc;
    --blue-light: #3fc0e6;
    --blue-deep: #0f8fcc;
    --band-dark: #141516;
    --band-mid: #3a3c3f;
    --ink: #0b0b0c;
    --paper-text: #f2f4f5;
    --rule: #8a8d90;
  }
  * { margin: 0; padding: 0; box-sizing: border-box; }
  html, body { width: 1200px; height: 892px; overflow: hidden; }
  body {
    background: var(--stage);
    font-family: "Arimo", Arial, sans-serif;
    position: relative;
  }
  .card {
    position: absolute;
    top: 291px;
    width: 540px;
    height: 309px;
    overflow: hidden;
    box-shadow: 0 6px 18px rgba(0,0,0,.18);
  }
  .card--front { left: 40px; background: linear-gradient(160deg, var(--blue) 0%, var(--blue-light) 55%, var(--blue-deep) 100%); }
  .card--back { left: 620px; background: linear-gradient(180deg, var(--blue) 0%, var(--blue-deep) 100%); }
  .card__band { position: absolute; inset: 0; width: 540px; height: 309px; }
  .company {
    position: absolute;
    font-weight: 700;
    color: var(--ink);
    letter-spacing: -0.3px;
    line-height: 1;
    white-space: nowrap;
  }
  .card--front .company { top: 10px; right: 22px; font-size: 28px; }
  .card--back .company { top: 50%; left: 50%; transform: translate(-50%, -50%); font-size: 46px; }
  .contact {
    position: absolute;
    color: var(--paper-text);
    font-size: 11px;
    line-height: 1.4;
    white-space: nowrap;
  }
  .contact__icon { display: block; width: 14px; height: 14px; margin-bottom: 4px; }
  .contact--web { left: 95px; top: 34px; }
  .contact--phone { left: 262px; top: 118px; }
  .contact--address { left: 375px; top: 178px; }
  .divider { position: absolute; height: 1px; background: var(--rule); width: 40px; }
  .divider--one { left: 210px; top: 104px; transform: rotate(35deg); }
  .divider--two { left: 330px; top: 168px; transform: rotate(35deg); }
  .person { position: absolute; left: 36px; top: 232px; color: var(--ink); line-height: 1.15; }
  .person__name { font-size: 19px; }
  .person__title { font-size: 14px; }
</style>
</head>
<body>
  <section class="card card--front">
    <svg class="card__band" viewBox="0 0 540 309" aria-hidden="true">
      <defs>
        <linearGradient id="bandShade" x1="0" y1="0" x2="1" y2="1">
          <stop offset="0" stop-color="var(--band-mid)"/>
          <stop offset="0.5" stop-color="var(--band-dark)"/>
          <stop offset="1" stop-color="#050505"/>
        </linearGradient>
      </defs>
      <path d="M270,0 Q440,0 540,180 L540,290 Q200,250 50,0 Z" fill="url(#bandShade)"/>
    </svg>

    <div class="company">VKT Consulting</div>

    <div class="contact contact--web">
      <svg class="contact__icon" viewBox="0 0 14 14"><circle cx="7" cy="7" r="6.5" fill="var(--blue)"/><circle cx="7" cy="7" r="2.2" fill="none" stroke="var(--band-dark)" stroke-width="1.3"/></svg>
      www.vktconsulting.com<br>info@vktconsulting.com
    </div>
    <span class="divider divider--one"></span>

    <div class="contact contact--phone">
      <svg class="contact__icon" viewBox="0 0 14 14"><circle cx="7" cy="7" r="6.5" fill="var(--blue)"/><path d="M4.5,3.5 L6,3.5 L6.6,5.5 L5.7,6.3 Q6.6,8 7.9,8.6 L8.7,7.7 L10.5,8.3 L10.5,9.8 Q7.5,10.5 5,8 Q3.5,5.7 4.5,3.5 Z" fill="var(--band-dark)"/></svg>
      555.014.2270
    </div>
    <span class="divider divider--two"></span>

    <div class="contact contact--address">
      <svg class="contact__icon" viewBox="0 0 14 14"><path d="M7,1.5 L13,7 L11.2,7 L11.2,12.5 L2.8,12.5 L2.8,7 L1,7 Z" fill="var(--blue)"/><rect x="6" y="9" width="2" height="3.5" fill="var(--band-dark)"/></svg>
      14 Larch Lane Westvale<br>NSW 2999
    </div>

    <div class="person">
      <div class="person__name">Dana Melbrook</div>
      <div class="person__title">Principal</div>
    </div>
  </section>

  <section class="card card--back">
    <div class="company">VKT Consulting</div>
  </section>
</body>
</html>
```